KCA Waltz of our luminaries

My nonprofit social service agency is having a fun gala based on the TV show waltz of the luminaries, and we need the key design for an invitation. The event is a dinner and will have 7 local well-known people dance in a contest-like setting with a nationally known host. This does not need to be the final invitation (RSVP, list of dancers/hosts, etc.). All I need at this point is a great design for the cover to give this event an identity and entice people to attend and/or donate to the cause! Though our logo colors are blue/green/burgandy, this can use black/gold/silver/white as well. Our website is www.kcaohvalley.org if that helps explain who we are.

Also, it can be abstract. And it does not have to include ballroom dancers if the word mark or other graphics are eye catching.

Target Market(s)

Donors, upscale, higher income,45-70, men and women (though women will more likely make the decision to attend)

Industry/Entity Type

Tv

Requirements
Must have
• The wording to be incorporated into the invitation cover is:
Kindred Care Alliance
Celebrates Rising Strong Through Years with
Waltz of the Luminaries
hosted by Host Name (will give the final name when confirmed)

Saturday, November 8, 2014
7 pm
Marlowe Cincinnati Tidewater Court
Nice to have
• I'd like to see something other than ballroom dancers just to give my committee some options. Is it possible to show footprints of dancers (man's shoe with woman's high heels) as the design element? Something that can be used across the invite (rsvp card).
Should not have
• You have free range to create and have fun! If you use our logo colors, either choose one color as the focus, or just be sure to focus on green and burgandy together

```html
<!DOCTYPE html>
<html lang="en">
<head>
<meta charset="utf-8">
<title>Kindred Care Alliance – Waltz of our Luminaries</title>
<link rel="stylesheet" href="https://fonts.googleapis.com/css2?family=Great+Vibes&family=Arimo:wght@400&display=swap">
<style>
  :root {
    --stage: #000000;
    --paper: #ffffff;
    --ink: #111111;
    --blue: #1565c8;
    --burgundy: #98346a;
    --green: #3a9a3a;
    --leather-dark: #0c0c0c;
    --leather-mid: #5a5a5a;
    --string: #1a1a1a;
  }
  * { margin: 0; padding: 0; box-sizing: border-box; }
  html, body { width: 1200px; height: 900px; overflow: hidden; background: var(--stage); }
  .canvas { position: relative; width: 1200px; height: 900px; background: var(--stage); }
  .invitation {
    position: absolute; left: 290px; top: 25px; width: 594px; height: 849px;
    background: var(--paper); overflow: hidden;
    font-family: "Arimo", Arial, sans-serif; color: var(--ink);
  }
  .brand {
    position: absolute; top: 48px; left: 0; width: 100%;
    display: flex; justify-content: center; align-items: center; gap: 10px;
  }
  .brand-dot { width: 26px; height: 26px; border-radius: 50%; background: var(--burgundy); }
  .brand-name { font-size: 27px; color: var(--blue); letter-spacing: -0.3px; }
  .tagline {
    position: absolute; top: 106px; width: 100%; text-align: center; font-size: 17.5px;
  }
  .title { position: absolute; inset: 0; font-weight: 400; z-index: 2; }
  .title-waltz {
    position: absolute; left: 30px; top: 160px;
    font-family: "Great Vibes", cursive; font-size: 132px; line-height: 1; color: var(--blue);
  }
  .title-of {
    position: absolute; left: 268px; top: 307px;
    font-family: "Arimo", Arial, sans-serif; font-size: 28px; line-height: 1; color: var(--burgundy);
  }
  .title-luminaries {
    position: absolute; left: 358px; top: 268px;
    font-family: "Great Vibes", cursive; font-size: 60px; line-height: 1; color: var(--green);
  }
  .strings { position: absolute; left: 0; top: 0; z-index: 1; }
  .shoe { position: absolute; z-index: 3; border-radius: 6px; }
  .shoe-boot {
    left: 161px; top: 483px; width: 146px; height: 165px;
    background: linear-gradient(160deg, var(--leather-mid), var(--leather-dark) 60%);
  }
  .shoe-heel {
    left: 351px; top: 593px; width: 102px; height: 150px;
    background: linear-gradient(200deg, var(--leather-mid), var(--leather-dark) 60%);
  }
  .host { position: absolute; left: 40px; top: 655px; }
  .host-label { font-size: 28px; line-height: 32px; }
  .host-name { font-size: 22px; line-height: 26px; margin-top: 4px; letter-spacing: 0.5px; }
  .details { position: absolute; left: 0; top: 746px; list-style: none; }
  .detail { display: flex; align-items: center; height: 26px; font-size: 20px; }
  .detail-key { width: 30px; height: 22px; margin-right: 10px; }
  .detail--date .detail-key { background: var(--blue); }
  .detail--time .detail-key { background: var(--burgundy); }
  .detail--venue .detail-key { background: var(--green); }
</style>
</head>
<body>
<main class="canvas">
  <article class="invitation">
    <header class="brand">
      <span class="brand-dot" aria-hidden="true"></span>
      <span class="brand-name">kindred care alliance...</span>
    </header>
    <p class="tagline">Celebrates Rising Strong Through Years with</p>

    <h1 class="title">
      <span class="title-waltz">Waltz</span>
      <span class="title-of">of our</span>
      <span class="title-luminaries">Luminaries</span>
    </h1>

    <svg class="strings" width="594" height="849" viewBox="0 0 594 849" aria-hidden="true">
      <path d="M205 282 C 200 320, 232 340, 222 380 S 196 440, 210 470 L 212 486" fill="none" stroke="var(--string)" stroke-width="2.5"/>
      <circle cx="212" cy="488" r="4" fill="none" stroke="var(--string)" stroke-width="2"/>
      <path d="M432 330 C 420 360, 446 400, 420 450 S 380 540, 392 580 L 392 596" fill="none" stroke="var(--string)" stroke-width="2.5"/>
      <circle cx="392" cy="598" r="4" fill="none" stroke="var(--string)" stroke-width="2"/>
    </svg>

    <div class="shoe shoe-boot" role="img" aria-label="Black leather man's dress boot hanging from a string"></div>
    <div class="shoe shoe-heel" role="img" aria-label="Black patent woman's high-heeled pump hanging from a string"></div>

    <section class="host">
      <p class="host-label">hosted by</p>
      <p class="host-name">XXXXX XXXXXX</p>
    </section>

    <ul class="details">
      <li class="detail detail--date"><span class="detail-key"></span>Saturday, November 8, 2014</li>
      <li class="detail detail--time"><span class="detail-key"></span>7 pm</li>
      <li class="detail detail--venue"><span class="detail-key"></span>Marlowe Cincinnati Tidewater Court</li>
    </ul>
  </article>
</main>
</body>
</html>
```